Natural Supplement Co Needs Label Makeover

Our company's success began with our main product, an amino acid blend that aids in fat metabolism, called Vantorel. Since then we continue to expand the product line that now includes a detox called Vantopurge, and probiotic called Vantoflora, as well as 3 others, for a total of 6 products/ labels.
Our original design/logo had more of an 'old-timey' feel (see attached 2-product photo). We are looking for a fresh label design update for the product line which reflects the range of supplements as cohesive and individual parts of an overall health plan/strategy (see attached 'Logo Update Test' as just one idea we had in-house, you need not consider it as a starting point).

Target Market(s)

women 25-45

Industry/Entity Type

Health And Wellness

Requirements
Must have
• consistent theme with confident look
Nice to have
• Each product (ie. "Vantorel") has a few-word descriptor: ("Fat-Burning Amino Acids") that should be planned on including as part of each label.
Should not have
• NO 'streamlined' or graphic interpretations of the human body, or figurative image

```html
<!DOCTYPE html>
<html lang="en">
<head>
<meta charset="UTF-8">
<title>Vantopurge – Label</title>
<link rel="stylesheet" href="https://fonts.googleapis.com/css2?family=Encode+Sans+Semi+Condensed:wght@500;600;700&display=swap">
<style>
  :root {
    --canvas-bg: #efefef;
    --label-white: #ffffff;
    --label-mist: #eef1f4;
    --brand-blue: #2f80d0;
    --brand-blue-deep: #2566b4;
    --brand-blue-light: #4d9be0;
    --ink-dark: #2b2f36;
    --pill-top: #5a9be0;
    --pill-bottom: #2d6fc2;
  }
  * { margin: 0; padding: 0; box-sizing: border-box; }
  html, body {
    width: 960px;
    height: 1200px;
    overflow: hidden;
  }
  body {
    background: radial-gradient(ellipse at center, #ffffff 0%, var(--canvas-bg) 70%, #e2e2e2 100%);
    font-family: "Encode Sans Semi Condensed", "Arial Narrow", sans-serif;
    position: relative;
  }
  .label {
    position: absolute;
    left: 166px;
    top: 130px;
    width: 628px;
    height: 940px;
    background: linear-gradient(180deg, var(--label-white) 0%, var(--label-mist) 60%);
    border-top: 10px solid var(--brand-blue);
    overflow: hidden;
    box-shadow: 0 2px 10px rgba(0,0,0,0.08);
  }
  .label__band {
    position: absolute;
    left: 0;
    right: 0;
    top: 636px;
    bottom: 0;
    background: linear-gradient(180deg, var(--brand-blue-light) 0%, var(--brand-blue) 45%, var(--brand-blue-deep) 100%);
  }
  .label__text {
    position: absolute;
    left: 0;
    right: 0;
    text-align: center;
    line-height: 1;
  }
  .descriptor {
    top: 182px;
    font-size: 52px;
    font-weight: 500;
    color: var(--ink-dark);
    letter-spacing: 0.5px;
  }
  .product-name {
    top: 326px;
    font-size: 118px;
    font-weight: 700;
    color: var(--brand-blue);
    letter-spacing: -2px;
  }
  .ingredient-pill {
    position: absolute;
    left: 67px;
    top: 572px;
    width: 494px;
    height: 156px;
    border-radius: 78px;
    border: 4px solid #ffffff;
    background: linear-gradient(180deg, var(--pill-top) 0%, var(--pill-bottom) 100%);
    display: flex;
    align-items: center;
    justify-content: center;
    color: #ffffff;
    font-size: 60px;
    font-weight: 600;
    letter-spacing: 0.5px;
  }
  .claim {
    top: 768px;
    font-size: 38px;
    font-weight: 600;
    color: #ffffff;
  }
  .volume {
    top: 870px;
    font-size: 26px;
    font-weight: 500;
    color: #e6f0fb;
  }
</style>
</head>
<body>
  <div class="label">
    <div class="label__band"></div>
    <p class="label__text descriptor">FAT BURNING</p>
    <h1 class="label__text product-name">Vantopurge</h1>
    <div class="ingredient-pill">AMINO ACIDS</div>
    <p class="label__text claim">ALL NATURAL SUPPLEMENT</p>
    <p class="label__text volume">1 FL. OZ (30 ml)</p>
  </div>
</body>
</html>
```